Super Greens Label for Supplement Bottle

We want to design a front label for a health supplement bottle. The product is called Meadow Crunch Chews™. This will be a new product so there is no current website for the product. The focus is on supergreens that taste great and deliver support for energy, digestion, and immune defense.
We want it to be modern, vibrant and appealing.
Bottle size: standard size supplement CLEAR bottle size, with white child resistant cap and the label panel dimensions are 3” x 7”. The label should be primarily white and green, with a touch of red; (see color palettes)/it can also ONLY be white and green. See samples attached.
We are only focused on the front of the bottle design, not on the back, but leave space for the supplement panel and other text on the back.
So the text for the front of the bottle is:
RT Halvorsen's
Meadow Crunch Chews™
Super Greens Blend for:
Energy, Digestion, and Immune Support*
60 Gummies | Dietary Supplement
Raspberry Flavor Gummies
Off to side of the label:
Non-GMO
Vegan Friendly
Plant-Based
Gelatin Free
Colors
Designer to choose colors to be used in the design.
Look and feel
Each slider illustrates characteristics of the customer's brand and the style your logo design should communicate.

```html
<!DOCTYPE html>
<html lang="en">
<head>
<meta charset="utf-8">
<title>Meadow Crunch Chews – Front Label</title>
<link href="https://fonts.googleapis.com/css2?family=Anton&family=Montserrat:wght@700;800&display=swap" rel="stylesheet">
<style>
  :root {
    --bg: #f4f4f4;
    --label: #ffffff;
    --green-deep: #138c63;
    --green-mid: #3f9c78;
    --green-soft: #5fae8e;
    --mint-glow: #c6e6d8;
    --white: #ffffff;
  }
  html, body {
    margin: 0;
    width: 1200px;
    height: 960px;
    overflow: hidden;
    background: var(--bg);
  }
  .canvas {
    position: relative;
    width: 1200px;
    height: 960px;
  }
  .label {
    position: absolute;
    left: 250px;
    top: 50px;
    width: 700px;
    height: 860px;
    background: var(--label);
    box-shadow: inset 0 0 90px 20px var(--mint-glow);
    overflow: hidden;
    font-family: "Anton", "Arial Narrow", sans-serif;
    color: var(--green-deep);
  }
  .brand-name {
    position: absolute;
    left: 60px;
    top: 100px;
    width: 330px;
    margin: 0;
    font-size: 58px;
    line-height: 1;
    letter-spacing: 0.5px;
    text-transform: uppercase;
    color: var(--green-deep);
  }
  .product-name {
    position: absolute;
    left: 68px;
    top: 255px;
    margin: 0;
    font-size: 136px;
    line-height: 0.98;
    text-transform: uppercase;
    letter-spacing: 1px;
    background: linear-gradient(100deg, var(--green-deep) 0%, var(--green-soft) 55%, var(--green-deep) 100%);
    -webkit-background-clip: text;
    background-clip: text;
    color: transparent;
  }
  .product-name sup {
    font-size: 34px;
    vertical-align: top;
    line-height: 1.6;
  }
  .benefits {
    position: absolute;
    left: 72px;
    top: 672px;
    width: 600px;
    margin: 0;
    font-size: 27px;
    line-height: 1.05;
    text-transform: uppercase;
    color: var(--green-mid);
  }
  .count-block {
    position: absolute;
    left: 72px;
    top: 752px;
    display: flex;
    align-items: center;
    gap: 14px;
  }
  .count {
    font-size: 92px;
    line-height: 1;
    color: var(--green-mid);
  }
  .count-text {
    display: flex;
    flex-direction: column;
    gap: 8px;
  }
  .flavor {
    background: var(--green-soft);
    color: var(--white);
    font-size: 28px;
    line-height: 1;
    padding: 5px 12px;
    text-transform: uppercase;
  }
  .supplement {
    font-size: 28px;
    line-height: 1;
    padding-left: 12px;
    text-transform: uppercase;
    color: var(--green-mid);
  }
  .claims-strip {
    position: absolute;
    right: 40px;
    top: 0;
    width: 100px;
    height: 470px;
    background: var(--green-mid);
    border-radius: 0 0 50px 50px;
    display: flex;
    flex-direction: column;
    align-items: center;
    justify-content: space-around;
    padding: 20px 0 14px;
    box-sizing: border-box;
  }
  .claim {
    width: 78px;
    height: 78px;
    border: 2px solid var(--white);
    border-radius: 50%;
    display: flex;
    align-items: center;
    justify-content: center;
    text-align: center;
    color: var(--white);
    font-family: "Montserrat", "Arial", sans-serif;
    font-weight: 800;
    font-size: 12px;
    line-height: 1.05;
    text-transform: uppercase;
    box-sizing: border-box;
  }
  .claim--lg {
    font-size: 17px;
  }
  .claim--script {
    text-transform: none;
    font-weight: 700;
    font-size: 16px;
  }
</style>
</head>
<body>
<div class="canvas">
  <section class="label">
    <h2 class="brand-name">RT Halvorsen's</h2>

    <h1 class="product-name">Meadow<br>Crunch<br>Chews<sup>™</sup></h1>

    <p class="benefits">Super greens blend for energy, digestion,<br>and immune support*</p>

    <div class="count-block">
      <span class="count">60</span>
      <div class="count-text">
        <span class="flavor">Raspberry flavor gummies</span>
        <span class="supplement">Dietary supplement</span>
      </div>
    </div>

    <aside class="claims-strip">
      <div class="claim claim--lg">Non<br>GMO</div>
      <div class="claim">Vegan<br>Friendly</div>
      <div class="claim claim--script">plant<br>based</div>
      <div class="claim">Gelatin<br>Free</div>
    </aside>
  </section>
</div>
</body>
</html>
```